Aerospace Center needs app design

We need a design that would be a creative and innovative look of a simple idea connecting air traffic control situations with sonification.
We would like to see designs that use the elements shown in the short video which are different pads, showing 4 different colors, connecting with a degree and feeling of urgency. The different pads will be movable over screen, similar as to a whiteboard where you can move things around. Each of those pads has 4 different elements that are shown:
- ATC Event (you can chose different setups)
- Select a status (you can chose between Information, Caution and Alert. Color needs to feel more alert from Information to Alert.
- Notes box (you can open the box and write additional text on it)
- Music (you can chose different files. on the right side you can see a small group of notes. When you hover over the notes, music will be played without pressing a play or stop button.
The second video is an overview of music archival program that is connected with the pads.
Look and feel
Each slider illustrates characteristics of the customer's brand and the style your logo design should communicate.

```html
<!DOCTYPE html>
<html lang="en">
<head>
<meta charset="utf-8">
<title>VEKTA – Sonification Pads</title>
<link href="https://fonts.googleapis.com/css2?family=Roboto:wght@400;500&display=swap" rel="stylesheet">
<style>
:root{
  --sidebar:#033a5e;
  --sidebar-top:#021a30;
  --sidebar-line:#0a4a72;
  --sidebar-text:#c9d7e6;
  --page:#f6f6f6;
  --header:#f7f7f7;
  --white:#ffffff;
  --text:#444;
  --muted:#777;
  --pad-1:#03a9f4;
  --pad-2:#8bc34a;
  --pad-3:#ff9800;
  --pad-4:#3f51b5;
  --badge-orange:#ffa21a;
  --badge-red:#f44336;
}
*{box-sizing:border-box;margin:0;padding:0}
html,body{width:1200px;height:766px;overflow:hidden}
body{font-family:'Roboto',sans-serif;background:var(--page);position:relative}
.sidebar{position:absolute;left:0;top:0;width:237px;height:766px;background:var(--sidebar)}
.brand{height:97px;background:var(--sidebar-top);display:flex;align-items:center;justify-content:center;gap:10px;color:var(--white);font-size:34px;font-weight:400;letter-spacing:1px}
.brand-mark{width:18px;height:18px;background:var(--white);border-radius:50%}
.nav{list-style:none}
.nav li{height:55px;border-bottom:1px solid var(--sidebar-line);display:flex;align-items:center;padding-left:22px;color:var(--sidebar-text);font-size:13px;font-weight:500;letter-spacing:.2px}
.nav li:first-child{height:59px}
.nav svg{width:20px;height:20px;margin-right:15px;fill:var(--sidebar-text)}
.topbar{position:absolute;left:237px;top:0;width:963px;height:97px;background:var(--header);box-shadow:0 2px 4px rgba(0,0,0,.06)}
.search{position:absolute;left:73px;top:25px;width:555px;height:45px;border:1px solid #bdbdbd;border-radius:23px;background:var(--white);display:flex;align-items:center;padding:0 20px;color:#888;font-size:16px;justify-content:space-between}
.divider{position:absolute;top:25px;width:1px;height:43px;background:#e3e3e3}
.icon-btn{position:absolute;top:36px;width:20px;height:20px}
.badge{position:absolute;top:-4px;right:-6px;width:13px;height:13px;border-radius:50%;color:#fff;font-size:9px;text-align:center;line-height:13px}
.avatar{position:absolute;left:806px;top:24px;width:42px;height:42px;border-radius:50%;background:linear-gradient(135deg,#8a6a55,#3f3a36)}
.user{position:absolute;left:856px;top:38px;font-size:14px;color:var(--muted)}
.caret{position:absolute;left:937px;top:44px;border:4px solid transparent;border-top:5px solid var(--muted)}
.pad{position:absolute;top:157px;width:225px;height:308px;border-radius:18px;color:var(--white)}
.pad-head{height:49px;border-bottom:1px solid rgba(255,255,255,.2);display:flex;align-items:center;justify-content:space-between;padding:0 16px}
.pad-title{font-size:20px}
.pad-close{font-size:16px;font-weight:500}
.field{position:absolute;left:11px;width:203px;height:36px;background:var(--white);border-radius:3px;color:var(--text);font-size:12px;display:flex;align-items:center;justify-content:space-between;padding:0 11px}
.field .drop{border:4px solid transparent;border-top:5px solid #333;margin-top:5px}
.f1{top:71px}.f2{top:114px}.f3{top:157px}.f4{top:201px}
.music{position:absolute;left:156px;top:250px;width:58px;height:35px;border:1px solid var(--white);border-radius:4px;display:flex;align-items:center;justify-content:center}
.footer{position:absolute;left:237px;top:706px;width:963px;height:60px;background:var(--sidebar);color:var(--white);font-size:13px;font-weight:500;display:flex;align-items:center;justify-content:center}
.footer-code{position:absolute;right:10px;top:37px;font-size:13px}
</style>
</head>
<body>
<aside class="sidebar">
  <div class="brand"><span class="brand-mark"></span>VEKTA</div>
  <ul class="nav">
    <li><svg viewBox="0 0 20 20"><path d="M10 2 1 10h3v8h5v-5h2v5h5v-8h3z"/></svg>HOME</li>
    <li><svg viewBox="0 0 20 20"><path d="M2 4h16v14H2zM4 8v8h12V8zM5 1h2v4H5zm8 0h2v4h-2z"/></svg>SCHEDULER</li>
    <li><svg viewBox="0 0 20 20"><path d="m10 1 2.7 6 6.3.5-4.8 4.2 1.5 6.3L10 14.7 4.3 18l1.5-6.3L1 7.5 7.3 7z"/></svg>FAVORITES</li>
    <li><svg viewBox="0 0 20 20"><path d="M2 2h6L6 4l4 4-2 2-4-4-2 2zm16 0v6l-2-2-4 4-2-2 4-4-2-2zM2 18v-6l2 2 4-4 2 2-4 4 2 2zm16 0h-6l2-2-4-4 2-2 4 4 2-2z"/></svg>RECENT</li>
    <li><svg viewBox="0 0 20 20"><path d="M10 2a8 8 0 1 0 0 16 8 8 0 0 0 0-16zm4 9h-3v3H9v-3H6V9h3V6h2v3h3z"/></svg>CREATE</li>
    <li><svg viewBox="0 0 20 20"><path d="M1 2h1.5v15H19v1.5H1zm3 9h2v5H4zm3-4h2v9H7zm3 3h2v6h-2zm3-5h2v11h-2zm3 6h2v5h-2z"/></svg>MARKETING</li>
    <li><svg viewBox="0 0 20 20"><path d="M17 3v13l-5-3H6l1 5H4l-1-5H2V7h10z"/></svg>FORMS</li>
    <li><svg viewBox="0 0 20 20"><path d="M4 1h8l5 5v13H4zm1.5 1.5v15h10V7H11V2.5zM7 10h7v1.3H7zm0 3h7v1.3H7z"/></svg>LISTS</li>
    <li><svg viewBox="0 0 20 20"><path d="M8.5 1h3l.5 2.5 2 1 2.2-1.4 2 2-1.4 2.2 1 2L20 9.5v3l-2.5.5-1 2 1.4 2.2-2 2-2.2-1.4-2 1-.5 2.5h-3L8 18.5l-2-1-2.2 1.4-2-2L3.3 14l-1-2L0 11.5v-3L2.5 8l1-2L2 3.8l2-2L6.2 3.3l2-1zM10 7a3 3 0 1 0 0 6 3 3 0 0 0 0-6z"/></svg>ADMIN</li>
  </ul>
</aside>

<header class="topbar">
  <div class="search">Search
    <svg width="16" height="16" viewBox="0 0 16 16"><circle cx="6.5" cy="6.5" r="5" fill="none" stroke="#666" stroke-width="2"/><path d="m10 10 4.5 4.5" stroke="#666" stroke-width="2.2"/></svg>
  </div>
  <span class="divider" style="left:687px"></span>
  <div class="icon-btn" style="left:702px">
    <svg viewBox="0 0 20 20" width="20" height="20"><path d="M10 2a5 5 0 0 0-5 5v5l-2 3h14l-2-3V7a5 5 0 0 0-5-5zm-2 14a2 2 0 0 0 4 0z" fill="#777"/></svg>
    <span class="badge" style="background:var(--badge-orange)">8</span>
  </div>
  <span class="divider" style="left:740px"></span>
  <div class="icon-btn" style="left:757px">
    <svg viewBox="0 0 20 20" width="20" height="20"><path d="M2 5h16v11H2zm0 1 8 5 8-5" fill="#777" stroke="#f7f7f7" stroke-width="1"/></svg>
    <span class="badge" style="background:var(--badge-red)">6</span>
  </div>
  <span class="divider" style="left:793px"></span>
  <div class="avatar" role="img" aria-label="User profile photo"></div>
  <span class="user">Alex Moren</span>
  <span class="caret"></span>
</header>

<section class="pad" style="left:254px;background:var(--pad-1)">
  <div class="pad-head"><span class="pad-title">SO1</span><span class="pad-close">✖</span></div>
  <div class="field f1">Select atc Event<span class="drop"></span></div>
  <div class="field f2">Information<span class="drop"></span></div>
  <div class="field f3">Notes</div>
  <div class="field f4">Aria.....<span class="drop"></span></div>
  <div class="music"><svg width="32" height="28" viewBox="0 0 32 28" fill="none" stroke="#fff" stroke-width="1.6"><path d="M9 20V5l14-3v15"/><path d="M3 6V1l3 2"/><circle cx="6.5" cy="21" r="2.5" fill="#fff"/><circle cx="20.5" cy="18" r="2.5" fill="#fff"/><path d="M28 12V2l2 2"/><circle cx="26.5" cy="13" r="1.8" fill="#fff"/></svg></div>
</section>

<section class="pad" style="left:490px;background:var(--pad-2)">
  <div class="pad-head"><span class="pad-title">SO2</span><span class="pad-close">✖</span></div>
  <div class="field f1">Landing<span class="drop"></span></div>
  <div class="field f2">Information<span class="drop"></span></div>
  <div class="field f3">Notes</div>
  <div class="field f4">Aria....<span class="drop"></span></div>
  <div class="music"><svg width="32" height="28" viewBox="0 0 32 28" fill="none" stroke="#fff" stroke-width="1.6"><path d="M9 20V5l14-3v15"/><path d="M3 6V1l3 2"/><circle cx="6.5" cy="21" r="2.5" fill="#fff"/><circle cx="20.5" cy="18" r="2.5" fill="#fff"/><path d="M28 12V2l2 2"/><circle cx="26.5" cy="13" r="1.8" fill="#fff"/></svg></div>
</section>

<section class="pad" style="left:727px;background:var(--pad-3)">
  <div class="pad-head"><span class="pad-title">SO3</span><span class="pad-close">✖</span></div>
  <div class="field f1">Depature<span class="drop"></span></div>
  <div class="field f2">Caution<span class="drop"></span></div>
  <div class="field f3">Notes</div>
  <div class="field f4">Nocturn...<span class="drop"></span></div>
  <div class="music"><svg width="32" height="28" viewBox="0 0 32 28" fill="none" stroke="#fff" stroke-width="1.6"><path d="M9 20V5l14-3v15"/><path d="M3 6V1l3 2"/><circle cx="6.5" cy="21" r="2.5" fill="#fff"/><circle cx="20.5" cy="18" r="2.5" fill="#fff"/><path d="M28 12V2l2 2"/><circle cx="26.5" cy="13" r="1.8" fill="#fff"/></svg></div>
</section>

<section class="pad" style="left:964px;background:var(--pad-4)">
  <div class="pad-head"><span class="pad-title">SO4</span><span class="pad-close">✖</span></div>
  <div class="field f1">Moon<span class="drop"></span></div>
  <div class="field f2">Alert<span class="drop"></span></div>
  <div class="field f3">Notes</div>
  <div class="field f4">Bumble...<span class="drop"></span></div>
  <div class="music"><svg width="32" height="28" viewBox="0 0 32 28" fill="none" stroke="#fff" stroke-width="1.6"><path d="M9 20V5l14-3v15"/><path d="M3 6V1l3 2"/><circle cx="6.5" cy="21" r="2.5" fill="#fff"/><circle cx="20.5" cy="18" r="2.5" fill="#fff"/><path d="M28 12V2l2 2"/><circle cx="26.5" cy="13" r="1.8" fill="#fff"/></svg></div>
</section>

<footer class="footer">©2021 Company Name.All rights reserved.<span class="footer-code">C2</span></footer>
</body>
</html>
```